App Design - Career Prep Pal

We require an App Design for our new App called 'Hiring Helper'. This app is essentially an assistant to help Users prepare for job interviews, to help them get hired. <br/><br/>Users who download the App can view common Questions and Answers, save their favourite responses and also view common Interview Tips. <br/><br/>The vision for our App is for Users who are preparing for an interview (1 week before, 1 day before, even 1 hour before), are able to download, view and educate themselves on common questions and responses, and then be confident to land the job. <br/><br/>Our team has developed wireframes to help highlight what each screen should do and include. Please see attached document, which also highlights key requirements for the experience. Feel free to add/remove/edit what you see on these wireframes. Our preference is that you use Adobe XD please.<br/><br/>In terms of design guidelines, we want the experience to be simple, intuitive and 'memorable' to help Users to remember the questions/responses when they are in the interview. <br/><br/>The final design should communicate 'neat and clean professionalism'; we like the design of: jobvista net au<br/><br/>Thank you for reading! Good luck !

Target Market(s)

Professional job seekers

Font styles to use
Sans Serif

Colors

Designer to choose colors to be used in the design.

Requirements
Must have
• Please see my PixelGuild_UX file that I have uploaded
Nice to have
• Could you also please include some ideas on how we can incorporate Advertising into the app screens

```html
<!DOCTYPE html>
<html lang="en">
<head>
<meta charset="utf-8">
<title>Hiring Helper – View Questions &amp; Response</title>
<link rel="stylesheet" href="https://fonts.googleapis.com/css2?family=Poppins:wght@300;400;600;700&display=swap">
<style>
  :root {
    --page-bg: #ffffff;
    --screen-bg: #f8f9f8;
    --header-start: #7dff00;
    --header-end: #00ee00;
    --accent: #80ff00;
    --card-border: #8cff3a;
    --card-bg: #ffffff;
    --ink: #1e1e1e;
    --ink-soft: #2b2b2b;
    --white: #ffffff;
  }
  * { box-sizing: border-box; margin: 0; padding: 0; }
  html, body {
    width: 1200px; height: 1199px; overflow: hidden;
    background: var(--page-bg);
    font-family: "Poppins", sans-serif;
  }
  .canvas { position: relative; width: 1200px; height: 1199px; }
  .app-screen {
    position: absolute; left: 309px; top: 50px;
    width: 581px; height: 1100px;
    background: var(--screen-bg);
    border-radius: 56px;
    overflow: hidden;
    box-shadow: 0 10px 30px rgba(0,0,0,0.12);
  }
  .app-header {
    position: absolute; left: 0; top: 0; width: 100%; height: 154px;
    background: linear-gradient(90deg, var(--header-start), var(--header-end));
  }
  .status-time {
    position: absolute; left: 48px; top: 10px;
    font-size: 19px; font-weight: 700; color: var(--ink);
  }
  .status-icons { position: absolute; right: 54px; top: 12px; }
  .back-arrow { position: absolute; left: 24px; top: 72px; }
  .app-title {
    position: absolute; left: 0; right: 0; top: 66px;
    text-align: center; font-size: 38px; font-weight: 700; color: var(--white);
  }
  .section-title {
    position: absolute; left: 0; right: 0; top: 198px;
    text-align: center; font-size: 27px; font-weight: 600; color: var(--ink);
  }
  .section-subtitle {
    position: absolute; left: 0; right: 0; top: 243px;
    text-align: center; font-size: 19px; font-weight: 400; color: var(--ink-soft);
  }
  .category-card {
    position: absolute; width: 260px; height: 203px;
    background: var(--card-bg);
    border: 1.5px solid var(--card-border);
    border-radius: 12px;
    box-shadow: 4px 6px 12px rgba(0,0,0,0.12);
  }
  .category-card svg { position: absolute; left: 50%; top: 38px; transform: translateX(-50%); }
  .category-label {
    position: absolute; left: 0; right: 0; top: 155px;
    text-align: center; font-size: 20px; color: var(--ink);
  }
  .card-behavioural { left: 21px; top: 330px; }
  .card-situational { left: 297px; top: 330px; }
  .card-motivational { left: 21px; top: 594px; }
  .card-technical { left: 297px; top: 594px; }
  .view-all-button {
    position: absolute; left: 120px; top: 872px; width: 342px; height: 70px;
    background: var(--accent); border-radius: 14px;
    color: var(--white); font-size: 30px; font-weight: 300;
    display: flex; align-items: center; justify-content: center;
  }
</style>
</head>
<body>
<div class="canvas">
  <main class="app-screen">
    <header class="app-header">
      <span class="status-time">05:30 AM</span>
      <svg class="status-icons" width="90" height="24" viewBox="0 0 90 24" aria-hidden="true">
        <rect x="0" y="14" width="3" height="6" fill="#1e1e1e"/>
        <rect x="5" y="10" width="3" height="10" fill="#1e1e1e"/>
        <rect x="10" y="6" width="3" height="14" fill="#1e1e1e"/>
        <rect x="15" y="2" width="3" height="18" fill="#1e1e1e"/>
        <rect x="34" y="3" width="46" height="18" rx="9" fill="none" stroke="#1e1e1e" stroke-width="2.5"/>
        <rect x="81" y="9" width="4" height="6" rx="1" fill="#1e1e1e"/>
        <text x="57" y="17" text-anchor="middle" font-family="Poppins, sans-serif" font-size="13" font-weight="700" fill="#1e1e1e">50</text>
      </svg>
      <svg class="back-arrow" width="48" height="44" viewBox="0 0 48 44" aria-label="Back">
        <path d="M44 22H8M24 5L7 22l17 17" fill="none" stroke="#fff" stroke-width="6" stroke-linecap="round" stroke-linejoin="round"/>
      </svg>
      <h1 class="app-title">Hiring Helper</h1>
    </header>

    <h2 class="section-title">View Questions &amp; Response</h2>
    <p class="section-subtitle">Select your question category</p>

    <div class="category-card card-behavioural">
      <svg width="96" height="96" viewBox="0 0 96 96" aria-hidden="true">
        <circle cx="48" cy="22" r="21" fill="#80ff00"/>
        <path d="M1 96a47 47 0 0 1 94 0z" fill="#80ff00"/>
      </svg>
      <span class="category-label">Behavioural</span>
    </div>

    <div class="category-card card-situational">
      <svg width="84" height="84" viewBox="0 0 84 84" aria-hidden="true">
        <path d="M12 70V18A14 14 0 0 1 26 4h32a14 14 0 0 1 14 14v52z" fill="#80ff00"/>
        <rect x="2" y="74" width="80" height="10" rx="2" fill="#80ff00"/>
      </svg>
      <span class="category-label">Situational</span>
    </div>

    <div class="category-card card-motivational">
      <svg width="96" height="108" viewBox="0 0 96 108" aria-hidden="true">
        <circle cx="48" cy="46" r="46" fill="#80ff00"/>
        <path d="M28 80a20 20 0 0 0 40 0z" fill="#80ff00" stroke="#fff" stroke-width="2"/>
        <path d="M40 72v10M56 72v10M36 72h24" stroke="#fff" stroke-width="2.5"/>
      </svg>
      <span class="category-label">Motivational</span>
    </div>

    <div class="category-card card-technical">
      <svg width="108" height="108" viewBox="0 0 108 108" aria-hidden="true">
        <g fill="#80ff00">
          <rect x="45" y="0" width="18" height="108" rx="3"/>
          <rect x="45" y="0" width="18" height="108" rx="3" transform="rotate(45 54 54)"/>
          <rect x="45" y="0" width="18" height="108" rx="3" transform="rotate(90 54 54)"/>
          <rect x="45" y="0" width="18" height="108" rx="3" transform="rotate(135 54 54)"/>
          <circle cx="54" cy="54" r="40"/>
        </g>
        <circle cx="54" cy="54" r="22" fill="#fff"/>
      </svg>
      <span class="category-label">Technical</span>
    </div>

    <div class="view-all-button">View All</div>
  </main>
</div>
</body>
</html>
```